NEW Modern Sleek Business Card for VR Language Startup

Our startup is using VR to lead the next wave of world language education. We need a two-sided business card that introduces the larger organization (Brightloom Language Inc) and our contact info on one side and shows the product, Glimwoorld, on the other side.

Side 1 (contact info)= Brightloom Logo and Contact info (name, title, phone, email)

Side 2 (product)= Glimworld logo, text, and website
Text= Culturally Immersive Language Learning Games
Website= www.glimworld-play.com

Target Market(s)

Education, Technology

Contact Information for Business Card

Contact info will be updated upon approval of the design. For now, put this as a placeholder.

Perry Dunmore
Founder & CEO
pdunmore@quillpost-mail.net
(555)-014-2286

Font styles to use
Other font styles liked:
• Gibson and Century Gothic are the brand fonts

Requirements
Nice to have
• I would love to see cohesion between the design and colors of the two logos. I have attached a few business card designs that I like, so you can get a feel for my preferred style.

```html
<!DOCTYPE html>
<html lang="en">
<head>
<meta charset="utf-8">
<title>Brightloom Language – Business Card</title>
<link href="https://fonts.googleapis.com/css2?family=Lato:wght@400;700&family=Questrial&display=swap" rel="stylesheet">
<style>
  :root {
    --backdrop: #141415;
    --card: #1e1f21;
    --card-edge: #26272a;
    --white: #f4f4f6;
    --muted: #5a5b5f;
    --rule: #4a4b4f;
    --cyan: #2fc6ec;
    --orange: #ff7a2e;
    --magenta: #e84a8c;
    --violet: #7a5cf0;
    --pattern-top: #2a2b2e;
    --pattern-bottom: #1e1f21;
  }
  * { margin: 0; padding: 0; box-sizing: border-box; }
  html, body {
    width: 1200px; height: 1108px; overflow: hidden;
    background: var(--backdrop);
  }
  .canvas {
    position: relative; width: 1200px; height: 1108px;
    display: flex; justify-content: center; align-items: center; gap: 80px;
  }
  .card {
    position: relative; width: 400px; height: 680px;
    background: var(--card);
    border: 1px solid var(--card-edge);
    border-radius: 24px; overflow: hidden;
    font-family: "Lato", sans-serif; color: var(--white);
    display: flex; flex-direction: column; align-items: center;
  }

  /* Contact side */
  .brand {
    margin-top: 200px;
    display: flex; align-items: center; gap: 14px;
  }
  .brand-dot {
    width: 22px; height: 22px; border-radius: 50%;
    background: var(--orange);
  }
  .brand-name {
    font-family: "Questrial", sans-serif;
    font-size: 50px; letter-spacing: 2px; color: var(--white);
  }
  .contact { margin-top: 150px; text-align: center; width: 290px; }
  .person-name {
    font-family: "Questrial", sans-serif;
    font-size: 36px; letter-spacing: 0.5px; line-height: 1;
    background: linear-gradient(90deg, var(--orange), var(--magenta) 45%, var(--violet) 75%, var(--cyan));
    -webkit-background-clip: text; background-clip: text; color: transparent;
  }
  .person-title { font-size: 24px; margin-top: 6px; }
  .rule { height: 1px; background: var(--rule); margin: 18px 0; }
  .contact-line { font-size: 21px; line-height: 1.45; }

  /* Product side */
  .pattern-field {
    position: absolute; inset: 0 0 auto 0; height: 420px;
    background: linear-gradient(180deg, var(--pattern-top), var(--pattern-bottom));
  }
  .product { position: relative; margin-top: 400px; text-align: center; width: 300px; }
  .product-mark { display: flex; align-items: center; justify-content: center; gap: 12px; }
  .product-dot { width: 20px; height: 20px; border-radius: 50%; background: var(--cyan); }
  .product-name {
    font-family: "Questrial", sans-serif; font-size: 52px; color: var(--white);
  }
  .tagline {
    margin-top: 22px; font-size: 21px; font-weight: 700;
    text-transform: uppercase; line-height: 1.2; letter-spacing: 0.3px;
  }
  .website { font-size: 22px; color: var(--cyan); }
</style>
</head>
<body>
<main class="canvas">
  <section class="card card--contact">
    <div class="brand">
      <span class="brand-dot"></span>
      <span class="brand-name">Brightloom</span>
    </div>
    <div class="contact">
      <p class="person-name">PERRY DUNMORE</p>
      <p class="person-title">Founder &amp; CEO</p>
      <div class="rule"></div>
      <p class="contact-line">(555)-014-2286</p>
      <p class="contact-line">pdunmore@quillpost-mail.net</p>
    </div>
  </section>

  <section class="card card--product">
    <div class="pattern-field" role="img" aria-label="Faint repeating pattern of the product symbol"></div>
    <div class="product">
      <div class="product-mark">
        <span class="product-dot"></span>
        <span class="product-name">Glimworld</span>
      </div>
      <p class="tagline">Culturally Immersive<br>Language Learning Games</p>
      <div class="rule"></div>
      <p class="website">www.glimworld-play.com</p>
    </div>
  </section>
</main>
</body>
</html>
```